Business Card Design Project

Doctor, Pain Management. Need a new business card design with appointment info on the back. New address is 18 Corvell Road, Suite 304, Brisdale, NJ 07391. Right now I believe the rest of the information is staying the same.

```html
<!DOCTYPE html>
<html lang="en">
<head>
<meta charset="utf-8">
<title>Steadfast Pain Care – Business Card</title>
<link rel="stylesheet" href="https://fonts.googleapis.com/css2?family=Oswald:wght@600&family=Roboto:wght@400;500&family=Open+Sans:ital,wght@0,400;1,400&display=swap">
<style>
  :root {
    --page: #3a3a3c;
    --card-dark: #28251d;
    --card-light: #ffffff;
    --accent-cyan: #5ec8ef;
    --accent-yellow: #e9e233;
    --text-light: #f2f2f2;
    --text-form: #4a4a4a;
    --rule: #8a8a8a;
  }
  * { box-sizing: border-box; margin: 0; padding: 0; }
  html, body { width: 1200px; height: 900px; overflow: hidden; }
  body {
    background: var(--page);
    font-family: "Roboto", Arial, sans-serif;
    position: relative;
  }
  .card {
    position: absolute;
    left: 250px;
    width: 700px;
    height: 400px;
    overflow: hidden;
    box-shadow: 0 6px 18px rgba(0,0,0,.35);
  }
  /* Appointment side */
  .card--appointment { top: 35px; background: var(--card-dark); }
  .brand {
    height: 92px;
    display: flex;
    align-items: center;
    justify-content: center;
    gap: 14px;
  }
  .brand__dot {
    width: 26px; height: 26px; border-radius: 50%;
    background: var(--accent-cyan);
  }
  .brand__name {
    font-family: "Roboto", Arial, sans-serif;
    font-weight: 500;
    font-size: 30px;
    color: var(--accent-yellow);
    letter-spacing: .5px;
  }
  .form {
    position: absolute;
    top: 92px; left: 0; right: 0; bottom: 28px;
    background: var(--card-light);
    padding: 26px 40px 0 40px;
    color: var(--text-form);
    font-size: 18px;
  }
  .form__row { display: flex; align-items: flex-end; margin-bottom: 16px; }
  .form__label { white-space: nowrap; margin-right: 8px; }
  .form__line { flex: 1; border-bottom: 2px dotted var(--rule); height: 1px; margin-bottom: 5px; }
  .form__suffix { font-size: 14px; margin-left: 6px; }
  .form__row--time { margin-left: 330px; }
  .days { display: flex; justify-content: space-between; margin: 4px 0 22px; }
  .day { display: flex; align-items: center; gap: 6px; font-size: 16px; }
  .day__box { width: 18px; height: 14px; border: 1.5px solid #555; }
  .notice {
    font-family: "Open Sans", Arial, sans-serif;
    font-style: italic;
    font-size: 14px;
    text-align: center;
    line-height: 1.35;
    color: #333;
  }
  /* Contact side */
  .card--contact { top: 465px; background: var(--card-dark); color: var(--text-light); }
  .person { position: absolute; left: 60px; top: 120px; text-align: right; width: 250px; }
  .person__name {
    font-family: "Oswald", Arial, sans-serif;
    font-weight: 600;
    font-size: 30px;
    color: var(--accent-cyan);
    line-height: 1.1;
  }
  .person__title { font-size: 17px; font-weight: 500; color: var(--accent-yellow); margin-top: 4px; }
  .divider {
    position: absolute; left: 338px; top: 100px;
    width: 1px; height: 120px;
    background: linear-gradient(to bottom, transparent, #9a978c, transparent);
  }
  .contacts { position: absolute; left: 362px; top: 112px; list-style: none; }
  .contacts li { display: flex; align-items: center; gap: 12px; font-size: 18px; line-height: 25px; }
  .contacts svg { width: 16px; height: 16px; fill: var(--accent-cyan); flex: none; }
  .address {
    position: absolute; left: 60px; top: 300px;
    display: flex; align-items: center; gap: 10px; font-size: 19px;
  }
  .address svg { width: 16px; height: 22px; fill: var(--accent-cyan); }
</style>
</head>
<body>
  <section class="card card--appointment" aria-label="Appointment card">
    <header class="brand">
      <span class="brand__dot"></span>
      <span class="brand__name">Steadfast Pain Care</span>
    </header>
    <div class="form">
      <div class="form__row"><span class="form__label">Name :</span><span class="form__line"></span></div>
      <div class="form__row"><span class="form__label">Date:</span><span class="form__line"></span></div>
      <div class="form__row form__row--time"><span class="form__label">Time :</span><span class="form__line"></span><span class="form__suffix">AM/PM</span></div>
      <div class="days">
        <span class="day">Sun <span class="day__box"></span></span>
        <span class="day">Mon <span class="day__box"></span></span>
        <span class="day">Tue <span class="day__box"></span></span>
        <span class="day">Wed <span class="day__box"></span></span>
        <span class="day">Thu <span class="day__box"></span></span>
        <span class="day">Fri <span class="day__box"></span></span>
        <span class="day">Sat <span class="day__box"></span></span>
      </div>
      <p class="notice">Please give me 24 hours notice if you are unable to keep your appointment or<br>a cancellation fee may be charged.</p>
    </div>
  </section>

  <section class="card card--contact" aria-label="Contact card">
    <div class="person">
      <h1 class="person__name">LIWEN ZHAO, M.D., PH.D.</h1>
      <p class="person__title">Board Certified Anesthiologist</p>
    </div>
    <span class="divider"></span>
    <ul class="contacts">
      <li><svg viewBox="0 0 16 16"><path d="M3.5 1l3 3-1.5 2c1 2 3 4 5 5l2-1.5 3 3-2 2C7 15 1 9 1.5 3z"/></svg>973.555.0148</li>
      <li><svg viewBox="0 0 16 16"><rect x="4" y="1" width="8" height="4"/><rect x="1" y="6" width="14" height="6" rx="1"/><rect x="4" y="10" width="8" height="5"/></svg>973.555.0162</li>
      <li><svg viewBox="0 0 16 16"><path d="M1 3h14v10H1z M1 3l7 6 7-6" stroke="#28251d" stroke-width="1"/></svg>steadfastpc.office@mailbox.com</li>
      <li><svg viewBox="0 0 16 16"><circle cx="8" cy="8" r="7"/></svg>www.steadfastpaincare.com</li>
    </ul>
    <p class="address"><svg viewBox="0 0 16 22"><path d="M8 0a8 8 0 0 0-8 8c0 6 8 14 8 14s8-8 8-14a8 8 0 0 0-8-8zm0 11a3 3 0 1 1 0-6 3 3 0 0 1 0 6z"/></svg>18 Corvell Road, Suite 304, Brisdale, NJ 07391</p>
  </section>
</body>
</html>
```